Corbeck Aluminium Design Upgrade

- This is for a layout design of the home page only. No coding required.

- The design should be based around the attached HPID (home page information design) I've attached both a JPEG of this
- Information only is in RED text. Copy to go on the design in BLACK text. Some instructions are in the HPID. Please be creative!
- The design needs to be clean and spacious
- Use the logo provided. Please use the colours from the logos in the website design.
- I've attached some images to use as examples to use for home page gallery
- The product logos (Pelvane, Trimbough etc) showed in the HPV can be googled for a higher quality image if required.
- The header can be changed/altered - just needs to have all information as per logo, along with the phone number.

- Expected standard of design examples: (Please DO NOT copy these exactly – they are just examples)
http://www.halden-works.example.nz/
http://www.plinthcove.example.nz/
http://www.dusofern.example.nz/

Width of content will be 1100 pixels when implemented as a web page. Header height (without nav bar) 150-160 pixels.

The winning PSD file will have to be provided as follows…
1. Canvas size of 2000px x 2000px - 72ppi in Adobe Photoshop (CS5 compatible)
2. Width of content section is 1100px wide - centered in the canvas
3. Any button rollovers/hovers in the PSD as hidden layers.
4. All fonts used must be Google fonts (except for the header fonts).
5. You will need to supply the chosen home page plus one example page (example page as a style guide for how all other pages will look). Example page is only the header and navigational bar at the top, an empty sector in the middle with a column (180 px wide) which can be left or right aligned which means the main sector is 920 pixels wide, and then the footer at the bottom of the page.

```html
<!DOCTYPE html>
<html lang="en">
<head>
<meta charset="utf-8">
<title>Corbeck Aluminium</title>
<link href="https://fonts.googleapis.com/css2?family=Open+Sans:wght@400;600;700&display=swap" rel="stylesheet">
<style>
:root{
  --navy:#0a1e8c;
  --yellow:#f5ee1c;
  --red:#d2514f;
  --red-btn:#d94744;
  --card:#ececec;
  --heading:#0a2a7a;
  --text:#555;
  --footer:#262626;
  --footer-bar:#1c1c1c;
  --footer-text:#c8c8c8;
}
*{margin:0;padding:0;box-sizing:border-box}
html,body{width:800px;height:1200px;overflow:hidden}
body{position:relative;font-family:"Open Sans",sans-serif;background:#fff;color:var(--text)}
.header{position:absolute;left:0;top:0;width:800px;height:99px;background:var(--navy)}
.brand{position:absolute;left:52px;top:18px;display:flex;align-items:center;gap:10px}
.brand-name{color:#fff;font-weight:700;font-size:26px;line-height:1.05}
.brand-name small{display:block;font-size:12px;font-weight:600;color:var(--yellow);letter-spacing:.5px;margin-top:4px}
.brand-mark{width:40px;height:40px;background:var(--red-btn)}
.call{position:absolute;left:460px;top:33px;color:#fff;font-size:10px}
.call strong{display:block;color:var(--yellow);font-size:16px;font-weight:400;margin-top:2px}
.call svg{position:absolute;left:104px;top:10px}
.partner{position:absolute;left:604px;top:40px;color:#fff;font-size:18px;font-weight:400;letter-spacing:3px}
.nav{position:absolute;left:0;top:99px;width:800px;height:31px;background:var(--yellow);display:flex;padding-left:49px}
.nav a{font-size:8.3px;color:#555;text-decoration:none;line-height:31px;padding:0 7.5px;border-left:1px solid #d9d22c;text-transform:uppercase}
.nav a:last-child{border-right:1px solid #d9d22c}
.hero{position:absolute;left:0;top:130px;width:800px;height:361px;background:linear-gradient(180deg,#dfe4ea 0%,#c9ccd0 45%,#7c8a5c 78%,#4f7a2e 100%)}
.hero-sub{position:absolute;top:16px;width:100%;text-align:center;font-size:19px;color:#333}
.hero-title{position:absolute;top:46px;width:100%;text-align:center;font-size:24px;font-weight:700;color:#222;letter-spacing:.5px}
.hero-btn{position:absolute;left:261px;top:86px;width:278px;height:34px;background:var(--red-btn);color:#fff;font-size:13.5px;line-height:34px;text-align:center;border-radius:3px}
.dots{position:absolute;left:369px;top:333px;width:62px;height:15px;background:#222;border-radius:8px;display:flex;gap:6px;justify-content:center;align-items:center}
.dots i{width:6px;height:6px;border-radius:50%;background:#fff}
.dots i:first-child{background:none;border:1px solid #fff}
.partners{position:absolute;left:100px;top:515px;width:600px;display:flex;justify-content:space-between;align-items:center}
.partner-logo{font-size:11px;color:#c9282d;font-weight:600;letter-spacing:2px}
.badge{background:#c9c9c9}
.divider{position:absolute;left:49px;top:602px;width:703px;height:1px;background:#e2e2e2}
.card{position:absolute;width:218px;height:169px;background:var(--card);text-align:center}
.card h2{background:var(--red);color:#fff;font-weight:400;font-size:15px;height:34px;line-height:34px}
.card h3{color:var(--heading);font-size:10px;font-weight:600;margin:13px 0 7px}
.card p{font-size:7.4px;line-height:12.8px;padding:0 8px;margin-bottom:6px}
.footer{position:absolute;left:0;top:1018px;width:800px;height:138px;background:var(--footer);color:var(--footer-text);font-size:8.2px}
.links{position:absolute;top:15px;list-style:none;line-height:18px}
.links li::before{content:"• ";}
.vline{position:absolute;top:14px;width:1px;height:112px;background:#444}
.contact{position:absolute;left:299px;top:15px;line-height:18px}
.contact b{font-weight:400;color:#fff}
.seal{position:absolute;left:612px;top:20px;width:62px;height:62px;border-radius:50%;background:#c9282d}
.guarantee{position:absolute;left:535px;top:94px;width:216px;text-align:center;line-height:14px}
.bottom{position:absolute;left:0;top:1156px;width:800px;height:44px;background:var(--footer-bar);color:var(--footer-text);font-size:8.2px}
.bottom p{position:absolute;left:49px;top:15px}
.social{position:absolute;left:675px;top:11px;display:flex;gap:9px}
.social i{width:19px;height:19px;border-radius:50%;background:#3b6cc4}
</style>
</head>
<body>
<header class="header">
  <div class="brand">
    <div class="brand-name">Corbeck Aluminium<small>EXCELLENCE IN ALUMINIUM WINDOWS &amp; DOORS</small></div>
    <div class="brand-mark"></div>
  </div>
  <div class="call">Upper Hutt, Wellington<strong>(04) 555 0182</strong>
    <svg width="18" height="14" viewBox="0 0 18 14"><path d="M2 3c3-3 11-3 14 0l-2 3-3-1V3H7v2L4 6z" fill="#fff"/></svg>
  </div>
  <div class="partner">PELVANE</div>
</header>
<nav class="nav">
  <a>Home</a><a>About Us</a><a>New Homes</a><a>Commercial</a><a>Replacement Joinery</a><a>Double Glazing</a><a>Conservatories</a><a>Gallery</a><a>Free Quote</a><a>Contact</a>
</nav>
<section class="hero" role="img" aria-label="Photo of a white apartment building with aluminium windows, hedges and lawn">
  <div class="hero-sub">Ensuring style and functionality with your aluminium joinery</div>
  <div class="hero-title">COMMERCIAL JOINERY</div>
  <div class="hero-btn">Get a FREE Quote for your Joinery Needs</div>
  <div class="dots"><i></i><i></i><i></i><i></i></div>
</section>
<div class="partners">
  <span class="partner-logo">PELVANE</span>
  <span class="partner-logo" style="color:#8a5a35">TRIMBOUGH</span>
  <div class="badge" style="width:54px;height:54px;border-radius:50%;background:#1d3f6e"></div>
  <div class="badge" style="width:44px;height:52px;border-radius:50%;background:#d6d6d6"></div>
  <div class="badge" style="width:90px;height:16px;background:#d0d0d0"></div>
  <div class="badge" style="width:90px;height:16px;background:#1b2f9a"></div>
</div>
<div class="divider"></div>

<article class="card" style="left:50px;top:628px">
  <h2>NEW HOMES</h2>
  <h3>Building your dream home?</h3>
  <p>Corbeck Aluminium can provide a wide range of stylish and functional options to help you get your dream home.</p>
  <p>From glass sliding doors to aluminum window frames, the Corbeck Aluminium team will work closely with you to ensure you get the best result for your new home.</p>
</article>
<article class="card" style="left:292px;top:628px">
  <h2>COMMERCIAL</h2>
  <h3>Improve the presentation of your business!</h3>
  <p>Whether in retail, hospitality, accommodation, office building or any commercial premises, Corbeck Aluminium will help you find the perfect look for your business.</p>
  <p>Shop fronts, automatic doors, curtain walling, windows and doors - the team can do it all, and to an extremely high standard of workmanship.</p>
</article>
<article class="card" style="left:534px;top:628px">
  <h2>REPLACEMENT JOINERY</h2>
  <h3>Tired of your old windows and doors?</h3>
  <p>Enjoy the many benefits of quality aluminium joinery, installed by our team of experts.</p>
  <p>By replacing your current timber windows and doors, you can enjoy minimised maintenance and improved style and insulation with your new replacement joinery.</p>
</article>
<article class="card" style="left:170px;top:820px">
  <h2>DOUBLE GLAZING</h2>
  <h3>Enjoy the many benefits of double glazing...</h3>
  <p>Retro-fitting or installing new double glazed windows in your property will provide a number of benefits:</p>
  <p>A warmer home in winter, cooler home in summer, control of condensation, reduce UV damage, reduce outside noise - these are only some of the advantages to having double glazing in your home.</p>
</article>
<article class="card" style="left:413px;top:820px">
  <h2>CONSERVATORIES</h2>
  <h3>Enjoy the sun all year round!</h3>
  <p>Glass conservatories and sunrooms offer an ideal way to enjoy the heat of the sun, all year long.</p>
  <p>The Corbeck Aluminium team will come to your home, listen to your ideas and thoughts, and arrange the perfect design for your home.</p>
</article>

<footer class="footer">
  <ul class="links" style="left:51px"><li>Home</li><li>About</li><li>Testimonials</li><li>New Homes</li><li>Commercial</li><li>Replacement Joinery</li></ul>
  <ul class="links" style="left:173px"><li>Double Glazing</li><li>Conservatories</li><li>Gallery</li><li>Free Quote</li><li>Contact</li></ul>
  <div class="vline" style="left:270px"></div>
  <div class="contact">
    <b>CONTACT DETAILS</b><br>
    Phone : (04) 555 0182<br>
    Fax &nbsp;&nbsp;&nbsp;: (04) 555 0193<br>
    Physical Address : 41 Karaka Cres, Upper Hutt<br>
    Postal Address : PO Box 40218, Upper Hutt
  </div>
  <div class="vline" style="left:521px"></div>
  <div class="seal"></div>
  <p class="guarantee">We guarantee all our work. If there is ever a Contact problem, we will be back to provide a solution.</p>
</footer>
<div class="bottom">
  <p>Copyright &nbsp;©&nbsp; 2014 &nbsp; Corbeck Aluminium. &nbsp; All rights reserved.</p>
  <div class="social"><i></i><i></i><i></i></div>
</div>
</body>
</html>
```